Business Card Design

Business Card for professional consulting firm working with large financial institutions.

Target Market(s)

Executive buyers

Industry/Entity Type

Banking

Contact Information for Business Card

Mild creativity wanted. Not boring, but do elaborate artwork.

Font styles to use
Serif
Sans Serif

Colors

Designer to choose colors to be used in the design.

Requirements
Must have
• Standard business card features - company name, individual name, telephone, website, email, locations.
Nice to have
• Two colors
Should not have
• too many colors, fancy printing, cartoons.

```html
<!DOCTYPE html>
<html lang="en">
<head>
<meta charset="utf-8">
<title>Northgate Business Card</title>
<link href="https://fonts.googleapis.com/css2?family=Montserrat:wght@400;500;700&family=Noto+Serif:wght@400&display=swap" rel="stylesheet">
<style>
  :root {
    --page: #ecebe8;
    --card-white: #fbfbfb;
    --ink: #141414;
    --band: #0c0c0c;
    --muted: #a3a3a3;
    --rule: #c9c9c9;
    --back-grey: #bdbdbd;
    --logo-grey: #6f6f6f;
    --paper-white: #ffffff;
  }
  * { box-sizing: border-box; margin: 0; padding: 0; }
  html, body { width: 1200px; height: 950px; overflow: hidden; }
  body {
    background: var(--page);
    font-family: "Montserrat", Arial, sans-serif;
    color: var(--ink);
    position: relative;
  }
  .card {
    position: absolute;
    left: 280px;
    width: 640px;
    height: 366px;
    box-shadow: 0 6px 18px rgba(0,0,0,0.18);
    overflow: hidden;
  }
  .card--front { top: 90px; background: var(--card-white); }
  .card--back { top: 494px; background: var(--back-grey); }

  .front-band { position: absolute; inset: 0; width: 100%; height: 100%; }

  .front-logo {
    position: absolute;
    left: 0; top: 0;
    width: 330px; height: 366px;
    display: flex; align-items: center; justify-content: center;
    padding-top: 40px;
  }
  .wordmark {
    font-family: "Noto Serif", Georgia, serif;
    font-weight: 400;
    letter-spacing: 0.5px;
  }
  .front-logo .wordmark { font-size: 40px; color: var(--logo-grey); }

  .front-divider {
    position: absolute;
    left: 330px; top: 104px;
    width: 1px; height: 210px;
    background: var(--rule);
  }

  .contact {
    position: absolute;
    left: 362px; top: 118px;
  }
  .contact__name { font-weight: 700; font-size: 19px; letter-spacing: 0.5px; }
  .contact__title { font-weight: 500; font-size: 14px; color: var(--muted); margin-top: 3px; letter-spacing: 0.3px; }
  .contact__address { font-size: 13px; line-height: 19px; margin-top: 16px; }
  .contact__list { list-style: none; margin-top: 12px; }
  .contact__list li {
    display: flex; align-items: center; gap: 8px;
    font-size: 13px; line-height: 22px;
  }
  .contact__list svg { width: 12px; height: 12px; flex: none; }

  .back-logo {
    position: absolute; inset: 0;
    display: flex; align-items: center; justify-content: center;
  }
  .back-logo .wordmark { font-size: 64px; color: var(--paper-white); }
</style>
</head>
<body>

<section class="card card--front" aria-label="Business card front">
  <svg class="front-band" viewBox="0 0 640 366" preserveAspectRatio="none" aria-hidden="true">
    <path d="M0 0 H640 V10 C420 14 200 30 70 80 C40 92 14 104 0 112 Z" fill="var(--band)"/>
  </svg>

  <div class="front-logo">
    <span class="wordmark">northgate</span>
  </div>

  <div class="front-divider"></div>

  <div class="contact">
    <p class="contact__name">DANIEL REYES</p>
    <p class="contact__title">CEO/FOUNDER</p>
    <p class="contact__address">4120 Alder Court<br>Juneau, Alaska 38215</p>
    <ul class="contact__list">
      <li>
        <svg viewBox="0 0 12 12" aria-hidden="true"><path d="M2.5 1 L4.5 1 L5.2 3.6 L4 4.6 C4.6 6 5.9 7.4 7.4 8 L8.4 6.8 L11 7.5 L11 9.5 C11 10.4 10.4 11 9.5 11 C5 11 1 7 1 2.5 C1 1.6 1.6 1 2.5 1 Z" fill="var(--ink)"/></svg>
        <span>512 804 3967</span>
      </li>
      <li>
        <svg viewBox="0 0 12 12" aria-hidden="true"><rect x="0.5" y="2" width="11" height="8" rx="1" fill="var(--ink)"/><path d="M1 2.6 L6 6.6 L11 2.6" stroke="var(--card-white)" stroke-width="1" fill="none"/></svg>
        <span>info@northgatepartners.com</span>
      </li>
      <li>
        <svg viewBox="0 0 12 12" aria-hidden="true"><circle cx="6" cy="6" r="5.5" fill="var(--ink)"/><path d="M0.8 6 H11.2 M6 0.5 C3.6 3 3.6 9 6 11.5 M6 0.5 C8.4 3 8.4 9 6 11.5" stroke="var(--card-white)" stroke-width="0.8" fill="none"/></svg>
        <span>www.northgatepartners.com</span>
      </li>
    </ul>
  </div>
</section>

<section class="card card--back" aria-label="Business card back">
  <div class="back-logo">
    <span class="wordmark">northgate</span>
  </div>
</section>

</body>
</html>
```